i need a business card for a plumbing company in california

we are a drain cleaning , maintenance plumbing company who is starting new marketing campaign for a tatrench-less pipe installation department .

Target Market(s)

the professional who appreciates time and quality workmanship.

Industry/Entity Type

Plumbing

Colors
0655a3
ec1f27

Requirements
Must have
• the second logo needs to be included
Nice to have
• a focus on the services offered
Should not have
• any underlined words on the brief

```html
<!DOCTYPE html>
<html lang="en">
<head>
<meta charset="utf-8">
<title>Clearline Pipe Works – Business Card</title>
<link rel="stylesheet" href="https://fonts.googleapis.com/css2?family=Mulish:wght@300;400;600;800&display=swap">
<style>
  :root {
    --brand-red: #ec1f27;
    --brand-red-deep: #c9252b;
    --brand-blue: #0655a3;
    --ink: #333333;
    --ink-soft: #555555;
    --divider: #8a8a8a;
    --card: #ffffff;
    --card-edge: #f1f1f1;
    --backdrop: #2b2b2b;
  }
  * { box-sizing: border-box; margin: 0; padding: 0; }
  html, body {
    width: 1200px;
    height: 997px;
    overflow: hidden;
    background: var(--backdrop);
    font-family: "Mulish", "Century Gothic", sans-serif;
  }
  .sheet {
    width: 1200px;
    height: 997px;
    display: flex;
    flex-direction: column;
    align-items: center;
    justify-content: center;
    gap: 60px;
  }
  .card {
    position: relative;
    width: 560px;
    height: 320px;
    background: linear-gradient(160deg, var(--card) 0%, var(--card-edge) 100%);
    overflow: hidden;
    box-shadow: 0 10px 30px rgba(0,0,0,0.45);
  }
  .card__swoosh {
    position: absolute;
    inset: 0;
    width: 100%;
    height: 100%;
  }
  .swoosh-blue { fill: var(--brand-blue); }
  .swoosh-red { fill: var(--brand-red-deep); }

  /* Back side */
  .card--back .company {
    position: absolute;
    left: 50px;
    top: 140px;
    font-size: 27px;
    font-weight: 600;
    letter-spacing: 0.5px;
    color: var(--brand-red-deep);
    text-transform: uppercase;
  }

  /* Front side */
  .card--front .company {
    position: absolute;
    left: 44px;
    top: 48px;
    font-size: 24px;
    font-weight: 800;
    letter-spacing: 0.4px;
    color: var(--brand-red-deep);
    text-transform: uppercase;
  }
  .person {
    position: absolute;
    left: 44px;
    top: 152px;
    text-align: right;
  }
  .person__name {
    font-size: 17px;
    font-weight: 400;
    color: var(--brand-red-deep);
    text-transform: uppercase;
    letter-spacing: 0.3px;
  }
  .person__title {
    font-size: 11px;
    color: var(--ink);
    margin-top: 2px;
  }
  .divider {
    position: absolute;
    left: 300px;
    top: 112px;
    width: 2px;
    height: 82px;
    background: linear-gradient(to bottom, transparent, var(--divider), transparent);
  }
  .contact {
    position: absolute;
    left: 318px;
    top: 104px;
    list-style: none;
    font-size: 11px;
    color: var(--ink-soft);
  }
  .contact__item {
    display: flex;
    align-items: center;
    gap: 8px;
    height: 22px;
  }
  .contact__icon {
    width: 14px;
    height: 14px;
    flex: none;
  }
  .contact__item--plain { padding-left: 22px; }
  .contact__address {
    margin-top: 4px;
    font-weight: 800;
    color: var(--brand-red-deep);
  }
</style>
</head>
<body>
<main class="sheet">

  <section class="card card--back" aria-label="Card back">
    <svg class="card__swoosh" viewBox="0 0 560 320" preserveAspectRatio="none" aria-hidden="true">
      <path class="swoosh-red" d="M250,300 C380,270 480,230 560,185 L560,198 C470,240 370,282 250,300 Z"/>
      <path class="swoosh-blue" d="M0,320 L560,320 L560,206 C430,268 250,305 0,316 Z"/>
    </svg>
    <h2 class="company">Clearline Pipe Works</h2>
  </section>

  <section class="card card--front" aria-label="Card front">
    <svg class="card__swoosh" viewBox="0 0 560 320" preserveAspectRatio="none" aria-hidden="true">
      <path class="swoosh-red" d="M230,300 C370,272 470,236 560,186 L560,200 C460,246 360,284 230,300 Z"/>
      <path class="swoosh-blue" d="M0,320 L560,320 L560,208 C430,270 250,306 0,316 Z"/>
    </svg>

    <h1 class="company">Clearline Pipe Works</h1>

    <div class="person">
      <p class="person__name">Daniel Serrano</p>
      <p class="person__title">Attorney at Law</p>
    </div>

    <div class="divider"></div>

    <ul class="contact">
      <li class="contact__item contact__item--plain">415.555.0142</li>
      <li class="contact__item">
        <svg class="contact__icon" viewBox="0 0 14 14" aria-hidden="true">
          <circle cx="7" cy="7" r="7" fill="var(--brand-red-deep)"/>
          <path d="M3.5,6 Q7,3 10.5,6 L9.5,7 L8.5,6 L5.5,6 L4.5,7 Z M4.5,7.5 L9.5,7.5 L10,10 L4,10 Z" fill="#fff"/>
        </svg>
        <span>daniel@clearlinepipe.com</span>
      </li>
      <li class="contact__item">
        <svg class="contact__icon" viewBox="0 0 14 14" aria-hidden="true">
          <circle cx="7" cy="7" r="7" fill="var(--brand-red-deep)"/>
          <rect x="3.5" y="4.5" width="7" height="5" fill="#fff"/>
          <path d="M3.5,4.5 L7,7.5 L10.5,4.5" fill="none" stroke="var(--brand-red-deep)" stroke-width="0.8"/>
        </svg>
        <span class="contact__address">2210 Harbor View Rd., Oakland, CA 94607</span>
      </li>
    </ul>
  </section>

</main>
</body>
</html>
```